Redesign for existing homepage

We would like a redesign for our websites 2 column homepage
We provide engine repair and reconditioning services
We would like a cleaner, modern site that works well with our logo colors
Please see the attached brief for more info
Target Market(s)
25 - 45
Industry/Entity Type
Cleaner
Requirements
Must have
- Google Fonts

```html
<!DOCTYPE html>
<html lang="en">
<head>
<meta charset="utf-8">
<title>Harlow Engines – Engine repairs &amp; reconditioning</title>
<link href="https://fonts.googleapis.com/css2?family=Roboto+Slab:wght@400;700&display=swap" rel="stylesheet">
<style>
:root{
  --navy:#23253a;
  --yellow:#ffd400;
  --yellow-light:#ffd84a;
  --yellow-deep:#f9bf22;
  --accent-number:#f5b82e;
  --blue:#0a5cf5;
  --heading-blue:#1a5ee8;
  --ink:#222;
  --body:#777;
  --footer-bg:#e8e8e8;
  --white:#fff;
}
*{margin:0;padding:0;box-sizing:border-box}
html,body{width:1200px;height:1031px;overflow:hidden}
body{position:relative;font-family:"Roboto Slab",serif;background:var(--white);color:var(--ink)}
a{color:inherit;text-decoration:none}

.topbar{position:absolute;left:0;top:0;width:1200px;height:40px;background:var(--navy);color:var(--white);font-size:17px;white-space:nowrap}
.topbar .tagline{position:absolute;left:243px;top:9px;font-weight:700}
.topbar .callout{position:absolute;left:730px;top:9px;display:flex;align-items:center;gap:6px}
.topbar .callout strong{color:var(--accent-number);font-weight:400}

.navbar{position:absolute;left:0;top:40px;width:1200px;height:67px;background:linear-gradient(var(--yellow-light),var(--yellow-deep))}
.brand{position:absolute;left:74px;top:21px;display:flex;align-items:center;gap:8px;font-size:18px;font-weight:700;color:var(--navy);white-space:nowrap}
.brand .dot{width:20px;height:20px;border-radius:50%;background:var(--blue)}
.menu{position:absolute;left:262px;top:23px;display:flex;font-size:15px;color:#333;list-style:none;white-space:nowrap}
.menu li{margin-right:17px}
.menu li:nth-child(4),.menu li:nth-child(5){margin-right:23px}

.hero{position:absolute;left:0;top:107px;width:1200px;height:189px;background:linear-gradient(90deg,#e4e4e4,#f7f7f7 45%,#e2e2e2);border-bottom:1px solid #d6d6d6}
.hero .car{position:absolute;left:96px;top:8px;width:234px;height:180px;border-radius:40px 60px 20px 20px;background:radial-gradient(ellipse at 55% 50%,#2d3a66,#1c2440 60%,rgba(200,200,200,0) 72%)}
.hero h1{position:absolute;left:390px;top:22px;font-size:33px;line-height:41px;font-weight:700;color:var(--ink);white-space:nowrap}
.hero .btn-enquiry{position:absolute;left:396px;top:116px;width:196px;height:40px;background:var(--blue);color:var(--white);font-size:19px;font-weight:700;display:flex;align-items:center;justify-content:center}
.slider-dots{position:absolute;left:1074px;top:156px;display:flex;gap:8px}
.slider-dots span{width:14px;height:14px;border-radius:50%;background:#d3d3d3;border:2px solid #fff;box-shadow:0 0 2px #999}
.slider-dots span.active{background:var(--blue)}

.service{position:absolute;left:30px;top:358px;width:640px}
.service .photo{width:613px;height:260px;background:linear-gradient(135deg,#4f7f86,#2c3a3e 45%,#c9ccd2 75%,#8d9196)}
.service h2{margin-top:22px;font-size:20px;font-weight:700;color:var(--heading-blue)}
.service p{margin-top:26px;width:600px;font-size:16.5px;line-height:29px;color:var(--body)}

.btn-yellow{display:flex;align-items:center;justify-content:center;gap:18px;width:228px;height:56px;background:var(--yellow);color:var(--ink);font-size:17px;font-weight:700;box-shadow:0 3px 6px rgba(0,0,0,.25);white-space:nowrap}
.service .btn-yellow{position:absolute;left:0;top:480px}

.sidebar{position:absolute;left:743px;top:318px;width:457px;height:588px;background:var(--white);box-shadow:-22px 0 30px -18px rgba(0,0,0,.18)}
.feature{position:absolute;left:0;width:457px}
.feature .icon{position:absolute;left:30px;top:22px;width:72px;height:72px;border-radius:50%;background:radial-gradient(circle at 50% 35%,#fff,#e6e6e6);box-shadow:0 8px 6px -4px rgba(0,0,0,.55);display:flex;align-items:center;justify-content:center}
.feature h3{position:absolute;left:149px;top:22px;width:290px;font-size:20px;line-height:29px;font-weight:700;color:var(--heading-blue);white-space:nowrap}
.feature p{position:absolute;left:149px;top:81px;font-size:16.5px;line-height:29px;color:var(--ink)}
.feature.trade p{width:275px}
.feature.classic p{width:290px}
.feature .btn-yellow{position:absolute;left:147px}
.feature.trade{top:0}
.feature.trade .btn-yellow{top:178px}
.feature.classic{top:277px}
.feature.classic .btn-yellow{top:213px}

.footer{position:absolute;left:0;top:924px;width:1200px;height:107px;background:var(--footer-bg);font-size:14.5px;color:#333;white-space:nowrap}
.footer nav{position:absolute;left:30px;top:30px}
.footer nav a+a::before{content:"|";margin:0 10px}
.footer .copy{position:absolute;left:30px;top:66px}
.badge-square{position:absolute;left:987px;top:32px;width:40px;height:50px;background:#f4e23a;border:2px solid #333}
.badge-round{position:absolute;left:1040px;top:32px;width:86px;height:50px;border-radius:50%;background:#111}
</style>
</head>
<body>
<header class="topbar">
  <span class="tagline">Engine repairs &amp; reconditioning specialists</span>
  <span class="callout">
    <svg width="16" height="18" viewBox="0 0 24 24" aria-hidden="true"><path fill="#2a6cf0" d="M6.6 10.8a15 15 0 0 0 6.6 6.6l2.2-2.2c.3-.3.7-.4 1-.2 1.1.4 2.3.6 3.6.6.6 0 1 .4 1 1V20c0 .6-.4 1-1 1A17 17 0 0 1 3 4c0-.6.4-1 1-1h3.5c.6 0 1 .4 1 1 0 1.3.2 2.5.6 3.6.1.3 0 .7-.2 1z"/></svg>
    Call us to get your engine running perfectly! <strong>04 555 0147</strong>
  </span>
</header>

<div class="navbar">
  <a class="brand" href="#"><span class="dot"></span>Harlow Engines</a>
  <ul class="menu">
    <li><a href="#">Home</a></li>
    <li><a href="#">About Us</a></li>
    <li><a href="#">Private Vehicle Service &amp; Repair</a></li>
    <li><a href="#">Trade Customers</a></li>
    <li><a href="#">Race &amp; Classic Car Engines</a></li>
    <li><a href="#">Make an Enquiry</a></li>
    <li><a href="#">Contact Us</a></li>
  </ul>
</div>

<section class="hero">
  <div class="car" role="img" aria-label="Dark blue SUV"></div>
  <h1>Specialist engine repair &amp; reconditioning<br>To have your car running at its best</h1>
  <a class="btn-enquiry" href="#">Make An Enquiry</a>
  <div class="slider-dots"><span class="active"></span><span></span><span></span><span></span></div>
</section>

<section class="service">
  <div class="photo" role="img" aria-label="Mechanic working on a car engine"></div>
  <h2>Need service and repair for a private vehicle?</h2>
  <p>Don't put up with your vehicle making irregular noises or breaking down! You can contact us to pinpoint the problem with your vehicle and have it running smoothly. With a free appraisal and efficient repair, you can feel secure knowing that the job will be done right the first time!</p>
  <a class="btn-yellow" href="#">Read More
    <svg width="20" height="20" viewBox="0 0 20 20" aria-hidden="true"><circle cx="10" cy="10" r="10" fill="#111"/><path d="M8 5l5 5-5 5" stroke="#ffd400" stroke-width="2.4" fill="none"/></svg>
  </a>
</section>

<aside class="sidebar">
  <div class="feature trade">
    <div class="icon"><svg width="30" height="30" viewBox="0 0 24 24" aria-hidden="true"><circle cx="12" cy="8" r="5" fill="#333"/><path d="M2 22c0-6 4-8 10-8s10 2 10 8z" fill="#333"/></svg></div>
    <h3>Interested in becoming<br>a trade customer?</h3>
    <p>You can outsource your the specialist machining jobs to us at very competitive rates.</p>
    <a class="btn-yellow" href="#">Trade Customer
      <svg width="20" height="20" viewBox="0 0 20 20" aria-hidden="true"><circle cx="10" cy="10" r="10" fill="#111"/><path d="M8 5l5 5-5 5" stroke="#ffd400" stroke-width="2.4" fill="none"/></svg>
    </a>
  </div>
  <div class="feature classic">
    <div class="icon"><svg width="28" height="28" viewBox="0 0 24 24" aria-hidden="true"><path fill="#333" d="M6.6 10.8a15 15 0 0 0 6.6 6.6l2.2-2.2c.3-.3.7-.4 1-.2 1.1.4 2.3.6 3.6.6.6 0 1 .4 1 1V20c0 .6-.4 1-1 1A17 17 0 0 1 3 4c0-.6.4-1 1-1h3.5c.6 0 1 .4 1 1 0 1.3.2 2.5.6 3.6.1.3 0 .7-.2 1z"/></svg></div>
    <h3>Is your classic or race car<br>your passion?</h3>
    <p>Is your vintage car just sitting in your garage? Contact us to get the engine on your classic car or race car repaired or overhauled.</p>
    <a class="btn-yellow" href="#">Contact Us
      <svg width="20" height="20" viewBox="0 0 20 20" aria-hidden="true"><circle cx="10" cy="10" r="10" fill="#111"/><path d="M8 5l5 5-5 5" stroke="#ffd400" stroke-width="2.4" fill="none"/></svg>
    </a>
  </div>
</aside>

<footer class="footer">
  <nav>
    <a href="#">Home</a><a href="#">About Us</a><a href="#">Private Vehicle Service &amp; Repair</a><a href="#">Trade Customers</a><a href="#">Race &amp; Classic Car Engines</a><a href="#">Make an Enquiry</a><a href="#">Contact Us</a>
  </nav>
  <p class="copy">© 2014 Company Name ,All Rights reserved</p>
  <div class="badge-square" role="img" aria-label="Partner badge"></div>
  <div class="badge-round" role="img" aria-label="Association badge"></div>
</footer>
</body>
</html>
```